body therapist

I need to offer my services as a massage therapist at home, acclimating customer space aroma candles with music and everything else to bring comfort. 8 offer rituals like this: relaxing ritual, purifying ritual, ritual breast, facial and body cleansing ritual organic, ritual man, ritual feet, slimming ritual. Naraja handling colors, seawater, green, lavender

Target Market(s)

men and women, tired, stressed, looking for something new

Font styles to use
Decorative
Script

Colors
f37122
0493ce
abd037

Requirements
Must have
• detailing each massage
Nice to have
• simple and elegant

```html
<!DOCTYPE html>
<html lang="es">
<head>
<meta charset="utf-8">
<title>Rituales Serenia</title>
<link href="https://fonts.googleapis.com/css2?family=Cutive&family=Architects+Daughter&family=Raleway:wght@400&display=swap" rel="stylesheet">
<style>
  :root {
    --backdrop: #c8c8c8;
    --page: #ffffff;
    --lime: #a8cd37;
    --orchid: #c95fc4;
    --ink: #4a4a4a;
    --panel-top: #d9dadc;
    --panel-bottom: #ffffff;
    --tab: #e3e3e3;
    --stone: #5b5566;
    --leaf: #4f9a2a;
  }
  html, body {
    margin: 0;
    width: 1000px;
    height: 1200px;
    overflow: hidden;
    background: var(--backdrop);
  }
  .page {
    position: absolute;
    left: 112px;
    top: 40px;
    width: 783px;
    height: 1110px;
    background: var(--page);
    overflow: hidden;
  }
  .page-tab {
    position: absolute;
    left: 348px;
    top: 0;
    width: 88px;
    height: 68px;
    background: var(--tab);
    border-radius: 0 0 44px 44px;
    font: 400 20px "Raleway", sans-serif;
    color: #333;
    text-align: center;
    line-height: 92px;
  }
  .hero-photo {
    position: absolute;
    left: 0;
    top: 70px;
    width: 783px;
    height: 318px;
    background: linear-gradient(180deg, #ffffff 0%, #f1e6f2 45%, #dfe9cf 75%, #eeeeee 100%);
  }
  .lime-block {
    position: absolute;
    left: 40px;
    top: 366px;
    width: 725px;
    height: 560px;
    background: var(--lime);
  }
  .scene-art {
    position: absolute;
    left: 0;
    top: 0;
  }
  .ritual-panel {
    position: absolute;
    left: 95px;
    top: 307px;
    width: 316px;
    height: 735px;
    background: linear-gradient(180deg, var(--panel-top) 0%, var(--panel-bottom) 100%);
  }
  .panel-title {
    margin: 14px 0 0;
    font: 400 45px/50px "Cutive", serif;
    color: var(--orchid);
    text-align: center;
    letter-spacing: 1px;
  }
  .ritual-list {
    list-style: none;
    margin: 32px 0 0;
    padding: 0 10px 0 39px;
  }
  .ritual-list li {
    position: relative;
    font: 400 19px/34px "Architects Daughter", cursive;
    color: var(--ink);
  }
  .ritual-list li::before {
    content: "";
    position: absolute;
    left: -25px;
    top: 11px;
    width: 12px;
    height: 12px;
    background: var(--orchid);
  }
  .ritual-note {
    margin: 38px 10px 0 39px;
    font: 400 19px/30px "Architects Daughter", cursive;
    color: var(--ink);
  }
  .duration-tag {
    position: absolute;
    left: 0;
    top: 930px;
    width: 258px;
    height: 77px;
    background: var(--lime);
    color: #fff;
    font: 400 21px/29px "Raleway", sans-serif;
    box-sizing: border-box;
    padding: 10px 0 0 38px;
  }
</style>
</head>
<body>
  <div class="page">
    <div class="hero-photo" role="img" aria-label="Orquídeas lilas sobre tallos de bambú verde en fondo blanco"></div>
    <div class="page-tab">4</div>
    <div class="lime-block"></div>
    <svg class="scene-art" width="783" height="1110" viewBox="0 0 783 1110">
      <defs>
        <linearGradient id="stoneLeaf" x1="0" y1="0" x2="1" y2="0">
          <stop offset="0" stop-color="#6a6474"/>
          <stop offset="0.55" stop-color="var(--stone)"/>
          <stop offset="0.75" stop-color="#4d8f2b"/>
          <stop offset="1" stop-color="#6fb43a"/>
        </linearGradient>
      </defs>
      <path role="img" aria-label="Escultura de piedra serena rodeada de hojas verdes" d="M0 860 C120 640 420 480 783 457 L783 1110 L0 1110 Z" fill="url(#stoneLeaf)"/>
    </svg>
    <section class="ritual-panel">
      <h1 class="panel-title">RITUALES<br>SERENIA</h1>
      <ul class="ritual-list">
        <li>RITUAL PURIFICANTE</li>
        <li>RITUAL VINOTERAPIA</li>
        <li>RITUAL MAMA</li>
        <li>RITUAL WELLNESS PIES</li>
        <li>RITUAL DE VITALIDAD PARA EL</li>
        <li>RITUAL PAREJA SERENIA SPA</li>
      </ul>
      <p class="ritual-note">TODOS NUESTROS RITUALES INCLUYEN MASAJE FACIAL CON AROMATERAPIA AMBIENTACION CON VELAS, AROMAS Y MUSICOTERAPIA</p>
    </section>
    <div class="duration-tag">ENTRE UNA Y DOS<br>HORAS APROX</div>
  </div>
</body>
</html>
```